Business card design needed

This is a new business and a unique service.
The market is academic staff at universities in Australia.
The services include workshops, seminars, individual research planning, individual support to develop grant applications for major funding. I will travel to work with people or work electronically with individuals. I have a highly successful track record and am known in many universities for work done in the past.

Target Market(s)

university professorial staff and junior academic staff in australia

Industry/Entity Type

Travel

Contact Information for Business Card

The Scholar Summit
Charting Routes to Study Grants

Dr Helen T Brisk

www.scholarsummit.com.au
E: info@scholarsummit.com.au
Ph: 0438 602741

Requirements
Must have
• I want a classic simple design. Colours - clean shades of blue with a contrast (not browns or orange).
I want to see line used as the primary feature, diagonal or other acute angles through part of the card.
Fonts should be crisp, angular and highly readable. Use upper and lower case in all text (except email and web address)
A simple logo based on TSS would be good.
Card can be designed vertically if the design works best that way.

```html
<!DOCTYPE html>
<html lang="en">
<head>
<meta charset="utf-8">
<title>The Scholar Summit – Business Cards</title>
<link rel="stylesheet" href="https://fonts.googleapis.com/css2?family=Source+Sans+3:wght@400;600&display=swap">
<style>
  :root {
    --stage: #e9ebef;
    --navy: #1b3483;
    --navy-deep: #16296e;
    --blue-light: #4a7cc2;
    --paper: #f4f5f7;
    --paper-shade: #d9dbdf;
    --ink: #1e1e22;
    --white: #ffffff;
  }
  * { box-sizing: border-box; margin: 0; padding: 0; }
  html, body {
    width: 1200px;
    height: 900px;
    overflow: hidden;
    background: var(--stage);
    font-family: "Source Sans 3", "Myriad Pro", Arial, sans-serif;
  }
  .card {
    position: absolute;
    left: 320px;
    width: 560px;
    height: 320px;
    overflow: hidden;
    box-shadow: 0 6px 18px rgba(20, 30, 60, 0.18);
  }
  .card-front {
    top: 100px;
    background: linear-gradient(115deg, var(--navy-deep) 0%, var(--navy) 40%, var(--blue-light) 75%, var(--navy) 100%);
  }
  .card-back {
    top: 480px;
    background: linear-gradient(120deg, var(--paper) 0%, var(--white) 45%, var(--paper-shade) 100%);
  }
  .card-swoosh {
    position: absolute;
    inset: 0;
    width: 100%;
    height: 100%;
  }
  .brand {
    position: absolute;
    white-space: nowrap;
  }
  .brand-name {
    font-weight: 600;
    font-size: 21px;
    letter-spacing: 2.5px;
    text-transform: uppercase;
  }
  .brand-tagline {
    font-weight: 400;
    font-size: 17px;
    margin-top: 4px;
  }
  .card-front .brand { left: 130px; top: 132px; color: var(--white); }
  .card-back .brand { left: 44px; top: 68px; }
  .card-back .brand-name { color: var(--navy); font-size: 18px; }
  .card-back .brand-tagline { color: #333; font-size: 15px; margin-top: 2px; }
  .contact {
    position: absolute;
    right: 44px;
    top: 168px;
    text-align: right;
    color: var(--ink);
    font-size: 19px;
    line-height: 27px;
  }
  .contact-name { font-size: 25px; line-height: 34px; }
  .contact-label { color: var(--navy); font-weight: 600; margin-right: 4px; }
</style>
</head>
<body>

<section class="card card-front" aria-label="Business card front">
  <svg class="card-swoosh" viewBox="0 0 560 320" preserveAspectRatio="none" aria-hidden="true">
    <defs>
      <linearGradient id="front-swoosh" x1="0" y1="0" x2="1" y2="0">
        <stop offset="0" stop-color="#ffffff" stop-opacity="0"/>
        <stop offset="0.45" stop-color="#ffffff" stop-opacity="0.95"/>
        <stop offset="1" stop-color="#ffffff" stop-opacity="1"/>
      </linearGradient>
    </defs>
    <polygon points="0,0 560,0 560,4 140,56 60,30 0,24" fill="url(#front-swoosh)"/>
  </svg>
  <div class="brand">
    <div class="brand-name">The Scholar Summit</div>
    <div class="brand-tagline">Charting Routes to Study Grants</div>
  </div>
</section>

<section class="card card-back" aria-label="Business card back">
  <svg class="card-swoosh" viewBox="0 0 560 320" preserveAspectRatio="none" aria-hidden="true">
    <defs>
      <linearGradient id="back-swoosh" x1="0" y1="0" x2="1" y2="0">
        <stop offset="0" stop-color="#1b3483" stop-opacity="0"/>
        <stop offset="0.35" stop-color="#1b3483" stop-opacity="0.55"/>
        <stop offset="1" stop-color="#1b3483" stop-opacity="1"/>
      </linearGradient>
    </defs>
    <polygon points="20,0 560,0 560,4 140,48 80,26 20,22" fill="url(#back-swoosh)"/>
  </svg>
  <div class="brand">
    <div class="brand-name">The Scholar Summit</div>
    <div class="brand-tagline">Charting Routes to Study Grants</div>
  </div>
  <div class="contact">
    <div class="contact-name">Dr Helen T Brisk</div>
    <div>www.scholarsummit.com.au</div>
    <div><span class="contact-label">E:</span>info@scholarsummit.com.au</div>
    <div><span class="contact-label">P:</span> 0438 602741</div>
  </div>
</section>

</body>
</html>
```